Business Card Design for Occupational Medicine Start Up Company

We need to design a professional business card. We are a healthcare company providing occupational medicine services to blue collar industries. We are professional, efficient and high quality service providers.

Target Market(s)

Blue Collar Industry: Shipbuilding, Ports, Trucking Companies; The Executives and Safety Officers for these companies

Industry/Entity Type

Healthcare

Contact Information for Business Card

Logo, Name, Title, Email, Phone

Other font styles liked:
• Please match our Brand Guide

Requirements
Must have
• Our Company Colors and Logo

```html
<!DOCTYPE html>
<html lang="en">
<head>
<meta charset="UTF-8">
<title>Shiftwell Clinics – Business Card</title>
<link rel="stylesheet" href="https://fonts.googleapis.com/css2?family=Montserrat:wght@400;500;700&display=swap">
<style>
  :root {
    --bg: #e4e7e9;
    --card-white: #f4f4f5;
    --card-grey: #e2e3e5;
    --brand-blue: #1fafe6;
    --brand-blue-deep: #1c9fd8;
    --brand-navy: #1f2c7c;
    --ink-white: #ffffff;
    --shadow: 0 3px 8px rgba(0, 0, 0, 0.18);
  }
  * { box-sizing: border-box; margin: 0; padding: 0; }
  html, body {
    width: 1200px;
    height: 800px;
    overflow: hidden;
    background: var(--bg);
    font-family: "Montserrat", Arial, sans-serif;
  }
  .canvas { position: relative; width: 1200px; height: 800px; }

  .card {
    position: absolute;
    width: 431px;
    height: 270px;
    box-shadow: var(--shadow);
    overflow: hidden;
  }
  .card-front {
    left: 193px;
    top: 102px;
    background: linear-gradient(160deg, var(--card-grey) 0%, var(--card-white) 60%, #ffffff 100%);
  }
  .card-back {
    left: 567px;
    top: 424px;
    background: var(--brand-blue);
    display: flex;
    align-items: center;
    justify-content: center;
  }

  .front-band { position: absolute; inset: 0; }

  .brand {
    position: absolute;
    display: flex;
    align-items: center;
    gap: 12px;
  }
  .card-front .brand { left: 27px; top: 26px; }
  .brand-dot {
    width: 40px;
    height: 40px;
    border-radius: 50%;
    background: var(--brand-navy);
  }
  .brand-name {
    font-weight: 700;
    font-size: 16px;
    letter-spacing: 0.5px;
    color: var(--brand-navy);
  }
  .card-back .brand { position: static; gap: 16px; }
  .card-back .brand-dot { width: 58px; height: 58px; background: var(--ink-white); }
  .card-back .brand-name { font-size: 22px; color: var(--ink-white); }

  .holder {
    position: absolute;
    left: 27px;
    top: 161px;
    color: var(--ink-white);
  }
  .holder-name {
    font-weight: 500;
    font-size: 16.5px;
    letter-spacing: 0.6px;
  }
  .holder-title {
    margin-top: 6px;
    font-size: 10.5px;
    letter-spacing: 0.5px;
  }

  .divider {
    position: absolute;
    left: 209px;
    top: 133px;
    width: 1px;
    height: 110px;
    background: var(--ink-white);
  }

  .contacts {
    position: absolute;
    left: 241px;
    top: 143px;
    list-style: none;
  }
  .contact {
    display: flex;
    align-items: center;
    gap: 6px;
    height: 14px;
    margin-bottom: 9.6px;
    font-size: 8.8px;
    color: var(--ink-white);
  }
  .contact-icon {
    width: 14px;
    height: 14px;
    flex: none;
  }
</style>
</head>
<body>
<main class="canvas">

  <section class="card card-front" aria-label="Business card front">
    <svg class="front-band" width="431" height="270" viewBox="0 0 431 270" aria-hidden="true">
      <defs>
        <linearGradient id="bandShade" x1="0" y1="0" x2="0.4" y2="1">
          <stop offset="0" stop-color="#1c9dd6"/>
          <stop offset="0.55" stop-color="#1fafe6"/>
          <stop offset="1" stop-color="#1fafe6"/>
        </linearGradient>
      </defs>
      <path d="M0 102 H338 Q406 102 431 164 V270 H0 Z" fill="url(#bandShade)"/>
    </svg>

    <div class="brand">
      <span class="brand-dot"></span>
      <span class="brand-name">SHIFTWELL CLINICS</span>
    </div>

    <div class="holder">
      <p class="holder-name">NAME SURNAME</p>
      <p class="holder-title">POSITION</p>
    </div>

    <span class="divider"></span>

    <ul class="contacts">
      <li class="contact">
        <svg class="contact-icon" viewBox="0 0 14 14" aria-hidden="true">
          <rect width="14" height="14" rx="2.5" fill="#fff"/>
          <path d="M4.2 3.2 L5.6 3 L6.3 5 L5.4 5.7 Q6.2 7.6 8.2 8.6 L8.9 7.7 L10.9 8.4 L10.7 9.8 Q10.4 10.8 9 10.7 Q4.4 10 3.3 4.9 Q3.3 3.5 4.2 3.2 Z" fill="var(--brand-blue)"/>
        </svg>
        <span>+012 34567890</span>
      </li>
      <li class="contact">
        <svg class="contact-icon" viewBox="0 0 14 14" aria-hidden="true">
          <rect width="14" height="14" rx="2.5" fill="#fff"/>
          <rect x="3" y="4.3" width="8" height="5.4" fill="var(--brand-blue)"/>
          <path d="M3 4.3 L7 7.4 L11 4.3" fill="none" stroke="#fff" stroke-width="0.8"/>
        </svg>
        <span>email@yourcompany.com</span>
      </li>
      <li class="contact">
        <svg class="contact-icon" viewBox="0 0 14 14" aria-hidden="true">
          <rect width="14" height="14" rx="2.5" fill="#fff"/>
          <path d="M7 11.4 Q4.2 8 4.2 6 A2.8 2.8 0 0 1 9.8 6 Q9.8 8 7 11.4 Z" fill="var(--brand-blue)"/>
          <circle cx="7" cy="6" r="1" fill="#fff"/>
        </svg>
        <span>Company street</span>
      </li>
      <li class="contact">
        <svg class="contact-icon" viewBox="0 0 14 14" aria-hidden="true">
          <rect width="14" height="14" rx="2.5" fill="#fff"/>
          <g fill="none" stroke="var(--brand-blue)" stroke-width="0.8">
            <circle cx="7" cy="7" r="3.6"/>
            <ellipse cx="7" cy="7" rx="1.6" ry="3.6"/>
            <path d="M3.4 7 H10.6 M3.9 5.2 H10.1 M3.9 8.8 H10.1"/>
          </g>
        </svg>
        <span>www.companywebsite.com</span>
      </li>
    </ul>
  </section>

  <section class="card card-back" aria-label="Business card back">
    <div class="brand">
      <span class="brand-dot"></span>
      <span class="brand-name">SHIFTWELL CLINICS</span>
    </div>
  </section>

</main>
</body>
</html>
```